Technical Communications firm needs an article turned into a white paper

We want to redesign a 3-part blog series into a white paper that we can print for a conference. I've consolidated the three posts into the attached Word document.

We are looking for a light, easy to read design. Good use of graphics to support the message. I've added the graphics we used in the original post.

You can view them at
http://www.brightquillpages.com/blog/are-you-satisfied-with-your-dita-solution/

Target Market(s)

Product managers from High-tech, Finance, and Medical industries.

Industry/Entity Type

Information Technology

Colors

Designer to choose colors to be used in the design.

Requirements
Must have
• Must be modern, light, easy to read and slick design. Try to incorporate the graphics provided, but feel free to add more. Must retain the lists and tables.
• Must align with our website/brand.
• Must be easy to read. So not too busy.
• Please move all footnotes to endnotes. You'll need to rework the numbering.
Nice to have
• Awesome coverpage.
Should not have
• Hokey clipart. Not too heavy or hard to read.

```html
<!DOCTYPE html>
<html lang="en">
<head>
<meta charset="utf-8">
<title>Skill Development – Page 4</title>
<link href="https://fonts.googleapis.com/css2?family=Carlito:wght@400;700&display=swap" rel="stylesheet">
<style>
  :root {
    --navy: #1e1e96;
    --cyan: #1aa6e2;
    --ink: #2b2b2b;
    --rule: #9fb3c8;
    --paper: #ffffff;
    --green-light: #2f8a5c;
    --green-dark: #1c5a3c;
  }
  * { margin: 0; padding: 0; box-sizing: border-box; }
  html, body { width: 927px; height: 1200px; overflow: hidden; background: var(--paper); }
  body { font-family: "Carlito", "Calibri", sans-serif; color: var(--ink); position: relative; }

  .brand { position: absolute; left: 84px; top: 62px; display: flex; align-items: center; gap: 10px; }
  .brand-mark { width: 72px; height: 72px; border-radius: 50%; background: var(--navy); }
  .brand-name { font-weight: 700; font-size: 24px; line-height: 1; color: var(--navy); letter-spacing: 0.5px; }

  .margin-rule { position: absolute; left: 111px; top: 134px; width: 3px; height: 926px; background: var(--navy); }

  .page-label {
    position: absolute; left: 744px; top: 70px; width: 126px; height: 28px;
    border-top: 1px solid var(--rule); border-bottom: 1px solid var(--rule);
    text-align: center; font-weight: 700; font-size: 16px; line-height: 27px;
    color: var(--navy); letter-spacing: 1px;
  }

  .section-title {
    position: absolute; left: 178px; width: 692px; top: 156px;
    text-align: center; font-weight: 700; font-size: 49px; color: var(--navy);
  }
  .section-title .title-text { text-decoration: underline; text-decoration-thickness: 3px; text-underline-offset: 5px; }

  .hero {
    position: absolute; left: 182px; top: 233px; width: 691px; height: 291px;
    background: radial-gradient(ellipse at 50% 45%, var(--green-light), var(--green-dark));
  }

  .body-copy {
    position: absolute; left: 178px; width: 692px;
    font-size: 15.2px; line-height: 22.6px; text-align: justify;
  }
  .body-copy p { text-indent: 30px; }
  .intro { top: 540px; }
  .closing { top: 943px; }
  sup { font-size: 9px; line-height: 0; }

  .sub-heading {
    position: absolute; left: 178px; width: 692px; top: 728px;
    text-align: center; font-weight: 700; font-size: 32px; color: var(--navy);
    text-decoration: underline; text-decoration-thickness: 2px; text-underline-offset: 4px;
  }
  .lead { position: absolute; left: 178px; width: 692px; top: 774px; font-size: 15.2px; line-height: 22.6px; }

  .issue-list { position: absolute; left: 264px; top: 821px; list-style: none; font-size: 15.2px; line-height: 24.4px; }
  .issue-list li { position: relative; padding-left: 24px; }
  .issue-list li::before { content: "•"; position: absolute; left: 0; color: var(--navy); }

  .dot-row { position: absolute; left: 106px; width: 762px; top: 1072px; display: flex; justify-content: space-between; }
  .dot { width: 13px; height: 13px; border-radius: 50%; background: var(--navy); }
  .dot:nth-child(even) { background: var(--cyan); }
</style>
</head>
<body>
  <header class="brand">
    <span class="brand-mark"></span>
    <span class="brand-name">BRIGHTQUILL PAGES</span>
  </header>
  <div class="margin-rule"></div>
  <div class="page-label">PAGE&nbsp; 4</div>

  <h1 class="section-title">1)&nbsp; <span class="title-text">Skill Development</span></h1>

  <div class="hero" role="img" aria-label="Photo of a puzzled man looking up at a green chalkboard reading 'What am I supposed to do'"></div>

  <section class="body-copy intro">
    <p>This article is part of a series based on the results of a survey of more than 250 technical communication professionals conducted by The Copy Steward in 2017 entitled The DITA Satisfaction Survey<sup>1</sup>. In the survey, almost two-thirds of respondents voiced concerns with their DITA deployment.</p>
    <p>In our previous article, we introduced the overall results from the survey that pertain to users’ dissatisfaction with their DITA solution. In this article, we examine the top rated issues pertaining to skills development.</p>
  </section>

  <h2 class="sub-heading">Issues Related to Skills Development</h2>
  <p class="lead">The top-ranked reported issues fall under the category of skill development and training. These include</p>
  <ul class="issue-list">
    <li>How do I reuse content? Ranked 1st by 75% of respondents;</li>
    <li>How do I make DITA do what I want it to do? Ranked 2nd by 69% of respondents;</li>
    <li>Where can I get DITA training? Ranked 3rd by 64% of respondents; and</li>
    <li>How do I create DITA content? Ranked 8th by 56% of respondents.</li>
  </ul>

  <section class="body-copy closing">
    <p>This problem area is far and away the most pressing obstacle for a successful DITA deployment. Too often authors are left to figure out how to adapt to writing for DITA on their own. Organizations will normally invest in tools training—and may even opt for a short training</p>
  </section>

  <div class="dot-row" aria-hidden="true">
    <span class="dot"></span><span class="dot"></span><span class="dot"></span><span class="dot"></span><span class="dot"></span><span class="dot"></span><span class="dot"></span><span class="dot"></span><span class="dot"></span><span class="dot"></span><span class="dot"></span><span class="dot"></span><span class="dot"></span><span class="dot"></span><span class="dot"></span><span class="dot"></span><span class="dot"></span><span class="dot"></span><span class="dot"></span><span class="dot"></span><span class="dot"></span><span class="dot"></span><span class="dot"></span><span class="dot"></span><span class="dot"></span><span class="dot"></span><span class="dot"></span><span class="dot"></span><span class="dot"></span><span class="dot"></span><span class="dot"></span><span class="dot"></span><span class="dot"></span>
  </div>
</body>
</html>
```